Company Values - print for wall

We ned a print of our values on one of the walls in our office. Create a couple of suggestions that we can print on our walls.

Summary:
- See power point with values
- make two suggestion: one with only titles + one with titles and bulletpoints / use the "We" version)
- make a suggestion in a galaxy raiders theme
- see brand book for inspiration
- see images of office for inspiration

The company's values that we want to highlight are: 1. Exceed expectations 2. Execute with passion 3. Empower each other Exceed expectations:​ • We establish a good understanding of current expectations.​ • We provide helpful, honest, and timely feedback.​ • We deliver impressive quality.​ Execute with passion:​ • We embrace change.​ • We seek innovative solutions.​ • We inspire others with your actions and attitudes. ​ • We care about success. ​ • We are confident and humble. Empower each other:​ • We are available to help colleagues.​ • We are open-minded.​ • We seek and share information proactively.​ • We respect others’ time.​ This is in line with achieving the company vision: « Our vision is to make a difference for our customers through our highly customizable solutions for planning, execution, and analysis. It’s less about the software itself and more about customer success. Make better decisions faster with Kelvanmark. »​ Bjarne Olav Tveit, CEO Kelvanmark Company slogan: Better Decisions Faster​ It's a lot of text above, but what we what to emphasize most are the following text above and here again: exceed expectations, execute with passion, empower each other We can do something fun and cool with the Galaxy Raiders theme as this is internal - that's the visual that would work with the company culture.

Font styles to use
Sans Serif

Requirements
Nice to have
• - one suggestion with Montserrat font
- one suggestion in galaxy raiders font

```html
<!DOCTYPE html>
<html lang="en">
<head>
<meta charset="utf-8">
<title>Kelvanmark Core Values</title>
<link rel="stylesheet" href="https://fonts.googleapis.com/css2?family=Montserrat:wght@400;500;800&family=Orbitron:wght@900&display=swap">
<style>
  :root {
    --backdrop: #c6c6c6;
    --space-deep: #05070d;
    --space-mid: #141a26;
    --horizon-blue: #2c4266;
    --orange: #ee8a3a;
    --white: #ffffff;
    --line: #e6e6e6;
  }
  * { margin: 0; padding: 0; box-sizing: border-box; }
  html, body { width: 804px; height: 1200px; overflow: hidden; }
  body { background: var(--backdrop); font-family: "Montserrat", sans-serif; position: relative; }

  .poster {
    position: absolute; left: 10px; top: 45px; width: 784px; height: 1109px;
    overflow: hidden; background: var(--space-deep);
    box-shadow: 4px 6px 10px rgba(0,0,0,0.35);
  }
  .space-backdrop {
    position: absolute; inset: 0;
    background: radial-gradient(ellipse at 50% 35%, var(--space-mid) 0%, var(--space-deep) 70%);
  }
  .planet-area {
    position: absolute; left: 0; right: 0; top: 860px; bottom: 0;
    background: linear-gradient(180deg, rgba(44,66,102,0) 0%, rgba(44,66,102,0.55) 35%, rgba(20,28,42,0.9) 75%, var(--space-deep) 100%);
  }

  .brand {
    position: absolute; left: 0; width: 100%; top: 52px; text-align: center;
    font-weight: 800; font-size: 46px; color: var(--white); letter-spacing: -0.5px;
  }

  .headline {
    position: absolute; left: 22px; top: 931px; transform-origin: 0 0; transform: rotate(-90deg);
    font-weight: 800; font-size: 100px; line-height: 1; letter-spacing: 1px; white-space: nowrap;
  }
  .headline .core { color: var(--orange); }
  .headline .values { color: var(--white); }

  .timeline { position: absolute; left: 0; top: 0; width: 784px; height: 1109px; }

  .value { position: absolute; left: 266px; width: 500px; }
  .value-title {
    font-family: "Orbitron", sans-serif; font-weight: 900; font-size: 22px;
    color: var(--orange); letter-spacing: 0.3px; margin-bottom: 6px;
  }
  .value-points { list-style: none; }
  .value-points li {
    position: relative; padding-left: 16px; color: var(--white);
    font-size: 18px; line-height: 23px; margin-bottom: 8px; font-weight: 500;
  }
  .value-points li::before { content: "•"; position: absolute; left: 2px; top: 0; }
  .value-exceed { top: 259px; }
  .value-execute { top: 511px; }
  .value-empower { top: 801px; }

  .contact {
    position: absolute; left: 0; width: 100%; top: 1038px; text-align: center;
    color: var(--white); font-size: 20px; letter-spacing: 1px;
  }
</style>
</head>
<body>
  <main class="poster">
    <div class="space-backdrop"></div>
    <div class="planet-area" role="img" aria-label="Photograph of a planet surface glowing blue at the horizon"></div>

    <div class="brand">Kelvanmark</div>

    <h1 class="headline"><span class="core">CORE</span> <span class="values">VALUES</span></h1>

    <svg class="timeline" viewBox="0 0 784 1109" fill="none" stroke="#e6e6e6" stroke-width="2.5" stroke-linecap="round" stroke-linejoin="round">
      <line x1="194" y1="320" x2="194" y2="483"/>
      <line x1="194" y1="589" x2="194" y2="763"/>
      <circle cx="194" cy="267" r="53"/>
      <circle cx="194" cy="536" r="53"/>
      <circle cx="194" cy="816" r="53"/>
      <g class="icon-chart" transform="translate(0,5)">
        <rect x="172" y="262" width="9" height="14"/>
        <rect x="186" y="254" width="9" height="22"/>
        <rect x="200" y="246" width="9" height="30"/>
        <line x1="164" y1="284" x2="220" y2="284"/>
        <polyline points="168,256 184,244 194,248 218,232"/>
        <polyline points="210,232 218,232 218,240"/>
      </g>
      <g class="icon-gear" transform="translate(0,20)">
        <circle cx="194" cy="516" r="17"/>
        <circle cx="194" cy="516" r="7"/>
        <line x1="194" y1="491" x2="194" y2="499"/>
        <line x1="194" y1="533" x2="194" y2="541"/>
        <line x1="169" y1="516" x2="177" y2="516"/>
        <line x1="211" y1="516" x2="219" y2="516"/>
        <line x1="176" y1="498" x2="182" y2="504"/>
        <line x1="206" y1="528" x2="212" y2="534"/>
        <line x1="212" y1="498" x2="206" y2="504"/>
        <line x1="182" y1="528" x2="176" y2="534"/>
      </g>
      <g class="icon-fist" transform="translate(0,9)">
        <rect x="180" y="800" width="28" height="20" rx="5"/>
        <line x1="187" y1="800" x2="187" y2="808"/>
        <line x1="194" y1="800" x2="194" y2="808"/>
        <line x1="201" y1="800" x2="201" y2="808"/>
        <path d="M184 820 L184 832 L204 832 L204 820"/>
        <line x1="194" y1="782" x2="194" y2="792"/>
        <line x1="180" y1="786" x2="184" y2="794"/>
        <line x1="208" y1="786" x2="204" y2="794"/>
      </g>
    </svg>

    <section class="value value-exceed">
      <h2 class="value-title">EXCEED EXPECTATIONS:</h2>
      <ul class="value-points">
        <li>We establish a good understanding of<br>current expectations.</li>
        <li>We provide helpful, honest, and timely<br>feedback.</li>
        <li>We deliver impressive quality.</li>
      </ul>
    </section>

    <section class="value value-execute">
      <h2 class="value-title">EXECUTE WITH PASSION:</h2>
      <ul class="value-points">
        <li>We embrace change.</li>
        <li>We seek innovative solutions.</li>
        <li>We inspire others with your actions and attitudes.</li>
        <li>We care about success.</li>
        <li>We are confident and humble.</li>
      </ul>
    </section>

    <section class="value value-empower">
      <h2 class="value-title">EMPOWER EACH OTHER:</h2>
      <ul class="value-points">
        <li>We are available to help colleagues.</li>
        <li>We are open-minded.</li>
        <li>We seek and share information proactively.</li>
        <li>We respect others’ time.</li>
      </ul>
    </section>

    <p class="contact">post@kelvanmark.com</p>
  </main>
</body>
</html>
```